Velmor Spire Nine Flash website

we need a website to cater to 2 aspect of the business. We have Velmor spire residence and velmor spire office. For the office, we will get their inquire and arrange a face to face meetup to show them the office area for rent. For the residence side, it will need to be like staylane or roomvio.com. we want to allow them to book online for the date they need. We have a total of 10 different room configurations starting at $70 per night and up depending on the size of the room. example of the design is https://brisquelodge.com/

Target Market(s)

the website should have detail information on the layout, designs, and luxury of the building.

Industry/Entity Type

office and service appartment rental/lease

Coding

Coded - Design and coding required

Number of Pages Required

5+ page

Requirements
Must have
• a luxury perspective
Nice to have
• example https://brisquelodge.com/

```html
<!DOCTYPE html>
<html lang="en">
<head>
<meta charset="utf-8">
<title>Velmor Spire Nine</title>
<link rel="stylesheet" href="https://fonts.googleapis.com/css2?family=Roboto:wght@300;400;500;700&family=Roboto+Condensed:wght@700&family=Raleway:wght@300&display=swap">
<style>
:root{
  --gold:#d4a02f;
  --gold-dark:#8c6b2c;
  --ink:#3b3b3b;
  --ink-soft:#6b6b6b;
  --bg:#fbf7f5;
  --panel:#ffffff;
  --field:#f4f1ef;
  --line:#d9d2cc;
}
*{box-sizing:border-box;margin:0;padding:0}
html,body{width:1200px;height:2242px;overflow:hidden}
body{position:relative;background:var(--bg);font-family:'Roboto',sans-serif;color:var(--ink)}
.abs{position:absolute}
.glow{position:absolute;border-radius:50%;background:radial-gradient(circle,rgba(231,196,120,.55) 0%,rgba(240,214,160,.25) 45%,rgba(251,247,245,0) 70%)}
/* header */
.brand{left:77px;top:12px;width:86px;height:51px;background:#fff;display:flex;align-items:center;justify-content:center;gap:4px;font-size:8px;font-weight:500;color:var(--gold);letter-spacing:.2px}
.brand .dot{width:10px;height:10px;border:1px solid var(--gold);flex:none}
.nav{left:0;width:1200px;top:29px;display:flex;justify-content:center;gap:19px;font-size:13px;font-weight:500;color:var(--ink)}
.btn-contact{left:986px;top:23px;width:133px;height:29px;border-radius:8px;background:var(--gold);color:#fff;font-size:11px;font-weight:500;letter-spacing:.8px;display:flex;align-items:center;justify-content:center;gap:6px}
/* hero */
.hero{left:77px;top:84px;width:1043px;height:356px;border-radius:10px;background:linear-gradient(180deg,#5d5f63 0%,#6c7b8a 40%,#4a4540 75%,#2f2b28 100%)}
.hero-title{left:0;width:1200px;top:230px;text-align:center;font-family:'Roboto Condensed',sans-serif;font-weight:700;font-size:26px;line-height:30px;color:#fff}
.search{left:241px;top:370px;width:715px;height:157px;border-radius:8px;background:var(--field);box-shadow:0 6px 18px rgba(0,0,0,.08);overflow:hidden}
.search-tabs{height:70px;background:var(--panel);display:flex;justify-content:center;gap:54px;padding-top:20px;font-size:11.5px;color:var(--ink)}
.tab{display:flex;align-items:flex-start;gap:5px;height:30px;padding:0 4px}
.tab.active{border-bottom:2px solid var(--gold)}
.search-field{position:absolute;left:27px;top:90px;width:490px;height:47px;border:1px solid var(--line);border-radius:6px;background:#fff;display:flex;align-items:center;justify-content:space-between;padding:0 18px;font-size:13px}
.search-btn{position:absolute;left:529px;top:90px;width:160px;height:47px;border-radius:6px;background:var(--gold);color:#fff;font-size:11.5px;font-weight:500;letter-spacing:.8px;display:flex;align-items:center;justify-content:center;gap:6px}
/* rooms */
.section-rule{left:77px;top:545px;width:50px;height:2px;background:var(--gold)}
.rooms-title{left:77px;top:553px;font-size:27px;line-height:29px;font-weight:500;color:var(--ink)}
.rooms-title .tail{display:inline-block;width:50px;height:2px;background:var(--gold);vertical-align:bottom}
.card{top:634px;width:248px}
.card-photo{height:235px;border-radius:8px;position:relative}
.tag{position:absolute;left:10px;top:12px;padding:3px 12px;border-radius:12px;background:rgba(255,255,255,.25);color:#fff;font-size:11px;font-weight:500}
.fav{position:absolute;right:12px;top:12px}
.card-row{display:flex;justify-content:space-between;margin-top:12px;font-size:11.5px}
.card-row strong{font-weight:500}
.price{color:var(--gold)}
.card-size{margin-top:6px;font-size:11.5px;color:var(--ink-soft)}
.book{display:inline-block;margin-top:10px;padding:4px 10px;border-radius:3px;background:var(--gold);color:#fff;font-size:11px;font-weight:500}
.more{left:507px;top:983px;width:182px;height:39px;border:1.5px solid var(--line);border-radius:8px;display:flex;align-items:center;justify-content:center;gap:10px;font-size:12.5px;font-weight:500;color:var(--gold)}
/* office */
.office-title{left:78px;top:1097px;font-size:34px;line-height:47px;font-weight:500;color:var(--ink);letter-spacing:-.5px}
.office-text{left:78px;top:1201px;width:460px;font-size:20px;line-height:40px;font-weight:300;color:var(--ink);letter-spacing:-.4px}
.office-photo{left:580px;top:1075px;width:540px;height:309px;border-radius:4px;background:linear-gradient(160deg,#3d4044 0%,#8c9196 45%,#c9ced2 70%,#70757a 100%)}
/* discuss */
.team-photo-a{left:213px;top:1451px;width:319px;height:219px;border-radius:6px;background:linear-gradient(150deg,#e9e7e4 0%,#b9bec4 55%,#3c4250 100%)}
.team-photo-b{left:77px;top:1643px;width:318px;height:218px;border-radius:6px;background:linear-gradient(160deg,#c9ccc4 0%,#8f8a80 50%,#7a4a2a 100%)}
.discuss-title{left:580px;top:1451px;width:540px;font-size:34px;line-height:47px;font-weight:500;color:var(--ink);letter-spacing:-.6px}
.field{width:258px;height:55px;border:2px solid var(--line);border-radius:6px;padding-left:8px;display:flex;align-items:center;font-size:16.5px;color:var(--ink-soft);letter-spacing:-.4px}
.submit{left:580px;top:1823px;width:101px;height:37px;border-radius:6px;background:var(--gold);border:2px solid #f0d9a3;color:#fff;font-size:13px;font-weight:500;display:flex;align-items:center;justify-content:center;gap:8px}
/* footer */
.footer{left:0;top:1928px;width:1200px;height:314px;background:linear-gradient(180deg,#cf992a 0%,#b88a30 55%,#8a6a2e 100%);color:#fff}
.footer-brand{left:78px;top:80px;display:flex;align-items:center;gap:8px;font-size:18px;font-weight:400;color:#fff}
.footer-brand .dot{width:14px;height:14px;border:1.5px solid #fff;border-radius:50%}
.footer-text{left:80px;top:150px;width:275px;font-family:'Raleway',sans-serif;font-weight:300;font-size:10.5px;line-height:20px;color:#fff}
.col-title{top:92px;font-size:20px;font-weight:500}
.col-link{font-size:13.5px;font-weight:400;letter-spacing:.3px}
.loc-line{left:882px;top:166px;display:flex;align-items:center;gap:10px;font-size:11px;font-weight:300}
.socials{left:884px;top:218px;display:flex;gap:26px}
.social{width:24px;height:24px;border:2px solid #fff;border-radius:50%}
</style>
</head>
<body>

<div class="glow" style="left:-180px;top:300px;width:560px;height:560px"></div>
<div class="glow" style="left:90px;top:1420px;width:460px;height:460px"></div>

<header>
  <div class="abs brand"><span class="dot"></span>Velmor Spire Nine</div>
  <nav class="abs nav"><span>Design</span><span>Location</span><span>Experience</span><span>About Us</span><span>Register Now</span></nav>
  <div class="abs btn-contact">
    <svg width="11" height="11" viewBox="0 0 24 24" fill="none" stroke="#fff" stroke-width="2"><path d="M5 3h4l2 5-3 2a12 12 0 0 0 6 6l2-3 5 2v4a2 2 0 0 1-2 2A18 18 0 0 1 3 5a2 2 0 0 1 2-2z"/></svg>
    CONTACT US
  </div>
</header>

<section>
  <div class="abs hero" role="img" aria-label="Photo of a bright shared office with people working at long desks"></div>
  <h1 class="abs hero-title">From living spaces to offices.<br>Everything you need is at your fingertips</h1>
  <div class="abs search">
    <div class="search-tabs">
      <div class="tab active">
        <svg width="18" height="18" viewBox="0 0 24 24" fill="none" stroke="#6b6b6b" stroke-width="1.3"><path d="M3 21h18M6 21V9h5v12M11 21V4h7v17M13 7h3M13 10h3M13 13h3"/></svg>
        Appartement
      </div>
      <div class="tab">
        <svg width="18" height="18" viewBox="0 0 24 24" fill="none" stroke="#6b6b6b" stroke-width="1.3"><path d="M3 8l3-4h12l3 4H3zM4 8v12M20 8v12M8 12v8M16 12v8M8 12h8"/></svg>
        Office
      </div>
    </div>
    <div class="search-field">Search here
      <svg width="16" height="18" viewBox="0 0 24 24" fill="none" stroke="#d4a02f" stroke-width="2"><path d="M12 22s7-7 7-12a7 7 0 0 0-14 0c0 5 7 12 7 12z"/><circle cx="12" cy="10" r="2.5"/></svg>
    </div>
    <div class="search-btn">
      <svg width="12" height="12" viewBox="0 0 24 24" fill="none" stroke="#fff" stroke-width="2.5"><circle cx="10" cy="10" r="7"/><path d="M15 15l6 6"/></svg>
      SEARCH
    </div>
  </div>
</section>

<section>
  <div class="abs section-rule"></div>
  <h2 class="abs rooms-title">Take a Look into<br>Our Room<span class="tail"></span></h2>

  <article class="abs card" style="left:81px">
    <div class="card-photo" role="img" aria-label="Photo of a one bed room with sofa and kitchenette" style="background:linear-gradient(160deg,#d8d3cc 0%,#a89a88 55%,#4a4036 100%)">
      <span class="tag">F1201</span>
      <svg class="fav" width="20" height="18" viewBox="0 0 24 22" fill="none" stroke="#fff" stroke-width="1.8"><path d="M12 20S2 14 2 7.5A5 5 0 0 1 12 5a5 5 0 0 1 10 2.5C22 14 12 20 12 20z"/></svg>
    </div>
    <div class="card-row"><strong>Type C, One Bed Room</strong><span><span class="price">$39</span> per Day</span></div>
    <div class="card-size">Room Size : 47.00</div>
    <span class="book">Book Now</span>
  </article>

  <article class="abs card" style="left:343px">
    <div class="card-photo" role="img" aria-label="Photo of a room with large window, sofa and city view" style="background:linear-gradient(160deg,#8e959c 0%,#b9b4aa 50%,#3f3a34 100%)">
      <span class="tag">F1202</span>
      <svg class="fav" width="20" height="18" viewBox="0 0 24 22" fill="none" stroke="#fff" stroke-width="1.8"><path d="M12 20S2 14 2 7.5A5 5 0 0 1 12 5a5 5 0 0 1 10 2.5C22 14 12 20 12 20z"/></svg>
    </div>
    <div class="card-row"><strong>Type C, One Bed Room</strong><span><span class="price">$39</span> per Day</span></div>
    <div class="card-size">Room Size : 47.00</div>
    <span class="book">Book Now</span>
  </article>

  <article class="abs card" style="left:605px">
    <div class="card-photo" role="img" aria-label="Photo of a bedroom with bed, yellow cushions and patterned rug" style="background:linear-gradient(160deg,#7d858c 0%,#cfc8bd 50%,#453b30 100%)">
      <span class="tag">F1203</span>
      <svg class="fav" width="20" height="18" viewBox="0 0 24 22" fill="none" stroke="#fff" stroke-width="1.8"><path d="M12 20S2 14 2 7.5A5 5 0 0 1 12 5a5 5 0 0 1 10 2.5C22 14 12 20 12 20z"/></svg>
    </div>
    <div class="card-row"><strong>Type C, One Bed Room</strong><span><span class="price">$39</span> per Day</span></div>
    <div class="card-size">Room Size : 47.00</div>
    <span class="book">Book Now</span>
  </article>

  <article class="abs card" style="left:867px">
    <div class="card-photo" role="img" aria-label="Photo of a bright living room with teal rug and armchairs" style="background:linear-gradient(160deg,#e6e4df 0%,#c9c2b3 45%,#8fb9b0 100%)">
      <span class="tag">F1204</span>
      <svg class="fav" width="20" height="18" viewBox="0 0 24 22" fill="none" stroke="#fff" stroke-width="1.8"><path d="M12 20S2 14 2 7.5A5 5 0 0 1 12 5a5 5 0 0 1 10 2.5C22 14 12 20 12 20z"/></svg>
    </div>
    <div class="card-row"><strong>Type C, One Bed Room</strong><span><span class="price">$39</span> per Day</span></div>
    <div class="card-size">Room Size : 47.00</div>
    <span class="book">Book Now</span>
  </article>

  <div class="abs more">Look Another Room
    <svg width="20" height="10" viewBox="0 0 20 10" fill="none" stroke="#d4a02f" stroke-width="1.6"><path d="M0 5h18M14 1l4 4-4 4"/></svg>
  </div>
</section>

<section>
  <h2 class="abs office-title">So Many Office For You<br>And Your Team</h2>
  <p class="abs office-text">Regardless of whether you're a solo worker, building a startup, or &nbsp;managing a thriving corporation, our network enables you to work in &nbsp;close proximity to clients, coworkers, or loved ones.</p>
  <div class="abs office-photo" role="img" aria-label="Photo of an empty modern office with desks, chairs and tall windows"></div>
</section>

<section>
  <div class="abs team-photo-a" role="img" aria-label="Photo of three colleagues discussing over a laptop"></div>
  <div class="abs team-photo-b" role="img" aria-label="Photo of a team meeting around a wooden table"></div>
  <h2 class="abs discuss-title">Let's Discuss together and find the perfect office space for you.</h2>
  <div class="abs field" style="left:580px;top:1592px">Full Name</div>
  <div class="abs field" style="left:862px;top:1592px">Email Adress</div>
  <div class="abs field" style="left:580px;top:1669px">Company Name</div>
  <div class="abs field" style="left:862px;top:1669px">Full Name</div>
  <div class="abs field" style="left:580px;top:1745px">Location</div>
  <div class="abs field" style="left:862px;top:1745px">For How Many People ?</div>
  <div class="abs submit">Submit
    <svg width="20" height="10" viewBox="0 0 20 10" fill="none" stroke="#fff" stroke-width="1.6"><path d="M0 5h18M14 1l4 4-4 4"/></svg>
  </div>
</section>

<footer class="abs footer">
  <div class="abs footer-brand"><span class="dot"></span>Velmor Spire Nine</div>
  <p class="abs footer-text">Lorem ipsum dolor sit amet consectetur. Eu laoreet tempus purus nibh eros tincidunt amet metus aliquet. Neque nisl consequat faucibus fusce sagittis diam arcu urna donec. In purus viverra pellentesque arcu nec nibh placerat elementum. Sed dolor dui nunc proin dictum et nibh tortor.</p>

  <h3 class="abs col-title" style="left:566px">About</h3>
  <span class="abs col-link" style="left:566px;top:158px">Office</span>
  <span class="abs col-link" style="left:566px;top:191px">Appartemen</span>

  <h3 class="abs col-title" style="left:721px">Contact</h3>
  <span class="abs col-link" style="left:721px;top:159px">Snapgrid</span>
  <span class="abs col-link" style="left:721px;top:192px">Chatwell</span>
  <span class="abs col-link" style="left:721px;top:225px">Friendline</span>
  <span class="abs col-link" style="left:721px;top:259px">Email</span>

  <h3 class="abs col-title" style="left:882px">Location</h3>
  <div class="abs loc-line">
    <svg width="20" height="26" viewBox="0 0 24 30" fill="#fff"><path d="M12 29S2 17 2 10a10 10 0 0 1 20 0c0 7-10 19-10 19zm0-15a4 4 0 1 0 0-8 4 4 0 0 0 0 8z" fill-rule="evenodd"/></svg>
    Lorem ipsum dolor sit amet consectetur.
  </div>
  <div class="abs socials"><span class="social"></span><span class="social"></span><span class="social"></span><span class="social"></span></div>
</footer>

</body>
</html>
```